U.S. Popcorn company needs business cards

We are a popcorn company that manufactures popcorn and sells it to grocery stores worldwide. Our theme is "Americana" and our logo is U.S. route 66 which is the most famous highway in the U.S.

We would like the design to be simple and to use both sides. On the back side we would like to see just the logo and website. The front would be normal details

Target Market(s)

Wholesalers, grocers and distributors

Industry/Entity Type

Manufacture

Contact Information for Business Card

Business name: Prairie Lantern Popcorn
Phone: +1 555 308 4726
Email: Dale@prairielanternpopcorn.com
website: www.prairielanternpopcorn.com
Tag Line: "POPular for a reason"
Name: Dale Whitcombe
Title: Founder/President

Requirements
Must have
• Either this design should be fun or clean and simple. I will let you show me your thougths.
Nice to have
• Anything that ties in the real Hwy Route 66.
• Colors might need to be red, white and blue incorporated.
Should not have
• Not be too busy.

```html
<!DOCTYPE html>
<html lang="en">
<head>
<meta charset="utf-8">
<title>Prairie Lantern Popcorn — Business Card</title>
<link rel="stylesheet" href="https://fonts.googleapis.com/css2?family=Open+Sans:wght@400;600;700;800&display=swap">
<style>
  :root {
    --backdrop: #ececec;
    --card-red: #e31e25;
    --ink-white: #ffffff;
    --shadow: rgba(70, 0, 0, 0.55);
  }
  * { box-sizing: border-box; margin: 0; padding: 0; }
  html, body {
    width: 1200px;
    height: 900px;
    overflow: hidden;
    background: var(--backdrop);
    font-family: "Open Sans", Arial, sans-serif;
  }
  .business-card {
    position: absolute;
    left: 120px;
    top: 138px;
    width: 960px;
    height: 624px;
    background: var(--card-red);
    color: var(--ink-white);
    box-shadow: 0 10px 30px rgba(0,0,0,0.18);
  }
  .tagline {
    position: absolute;
    left: 38px;
    top: 44px;
    font-size: 29px;
    font-weight: 700;
    letter-spacing: -0.5px;
    text-shadow: 2px 2px 3px var(--shadow);
  }
  .person {
    position: absolute;
    left: 44px;
    top: 262px;
  }
  .person-name {
    font-size: 32px;
    font-weight: 600;
    line-height: 1.2;
  }
  .person-title {
    font-size: 25px;
    font-weight: 400;
    line-height: 1.25;
  }
  .contact-list {
    position: absolute;
    left: 44px;
    top: 486px;
    list-style: none;
  }
  .contact-item {
    display: flex;
    align-items: center;
    height: 37px;
    font-size: 25px;
    font-weight: 400;
  }
  .contact-icon {
    width: 20px;
    height: 20px;
    margin-right: 22px;
    fill: var(--ink-white);
    flex: none;
  }
  .brand-name {
    position: absolute;
    left: 490px;
    top: 220px;
    width: 420px;
    text-align: center;
    font-size: 54px;
    font-weight: 800;
    line-height: 1.1;
    color: var(--ink-white);
  }
</style>
</head>
<body>
  <main class="business-card">
    <p class="tagline">POPULAR FOR A REASON</p>

    <div class="person">
      <p class="person-name">Dale Whitcombe</p>
      <p class="person-title">Founder/President</p>
    </div>

    <ul class="contact-list">
      <li class="contact-item">
        <svg class="contact-icon" viewBox="0 0 24 24" aria-hidden="true"><path d="M6.6 10.8a15.1 15.1 0 0 0 6.6 6.6l2.2-2.2c.3-.3.7-.4 1-.2 1.1.4 2.3.6 3.6.6.6 0 1 .4 1 1V20c0 .6-.4 1-1 1A17 17 0 0 1 3 4c0-.6.4-1 1-1h3.5c.6 0 1 .4 1 1 0 1.3.2 2.5.6 3.6.1.3 0 .7-.2 1z"/></svg>
        <span>+1 555 308 4726</span>
      </li>
      <li class="contact-item">
        <svg class="contact-icon" viewBox="0 0 24 24" aria-hidden="true"><path d="M3 6h18v12H3z" fill="none"/><path d="M3 6h18v1.2l-9 6-9-6zM3 9.2l9 6 9-6V18H3z"/></svg>
        <span>Dale@prairielanternpopcorn.com</span>
      </li>
      <li class="contact-item">
        <svg class="contact-icon" viewBox="0 0 24 24" aria-hidden="true"><path d="M12 2a10 10 0 1 0 0 20 10 10 0 0 0 0-20zm0 2c.9 1.2 1.6 2.6 2 4h-4c.4-1.4 1.1-2.8 2-4zM4.3 14a8 8 0 0 1 0-4h3.4a16 16 0 0 0 0 4zm.8 2h3c.3 1.3.8 2.5 1.4 3.6A8 8 0 0 1 5.1 16zm3-8h-3a8 8 0 0 1 4.4-3.6C8.9 5.5 8.4 6.7 8.1 8zM12 20c-.9-1.2-1.6-2.6-2-4h4c-.4 1.4-1.1 2.8-2 4zm2.3-6H9.7a14 14 0 0 1 0-4h4.6a14 14 0 0 1 0 4zm.2 5.6c.6-1.1 1.1-2.3 1.4-3.6h3a8 8 0 0 1-4.4 3.6zM16.3 14a16 16 0 0 0 0-4h3.4a8 8 0 0 1 0 4z"/></svg>
        <span>www.prairielanternpopcorn.com</span>
      </li>
    </ul>

    <p class="brand-name">Prairie Lantern Popcorn</p>
  </main>
</body>
</html>
```